Brovanek Data Yellow rose letterhead

I have a new logo for my company but in its current form it is too large to be used on letterhead or as a email signature. I need to have the designer use elements from the current logo and create something close to the original but more suited for smaller items.
Updates

I just uploaded a copy of our logo that does not have the weathered affect. Thanks

Reason: More time for revisions

Industry/Entity Type

It Company

Requirements
Must have
• The design must maintain the visual effect of the current logo. It needs to include the yellow rose and the name of the company.
Nice to have
• It would be nice to maintain the stamp theme and incorporate my name, address, phone, email. etc.

```html
<!DOCTYPE html>
<html lang="en">
<head>
<meta charset="utf-8">
<title>Brovanek Data Letterhead</title>
<link rel="stylesheet" href="https://fonts.googleapis.com/css2?family=Questrial&display=swap">
<style>
  :root {
    --backdrop: #e8e5e0;
    --paper: #ffffff;
    --teal: #3bbcc1;
    --ink: #1c1c1c;
    --rose-gold: #f6b731;
    --brand-text: #ffffff;
  }
  * { box-sizing: border-box; margin: 0; padding: 0; }
  html, body {
    width: 1054px;
    height: 1200px;
    overflow: hidden;
    background: var(--backdrop);
  }
  .canvas {
    position: relative;
    width: 1054px;
    height: 1200px;
  }
  .letterhead {
    position: absolute;
    left: 117px;
    top: 20px;
    width: 820px;
    height: 1160px;
    background: var(--paper);
    box-shadow: 0 4px 14px rgba(0, 0, 0, 0.18);
    overflow: hidden;
  }
  .header-band {
    position: absolute;
    left: 0;
    top: 0;
    width: 820px;
    height: 120px;
    display: block;
  }
  .header-band path { fill: var(--teal); }
  .brand {
    position: absolute;
    right: 48px;
    top: 28px;
    display: flex;
    align-items: center;
    gap: 12px;
    font-family: "Questrial", sans-serif;
    font-size: 28px;
    line-height: 34px;
    letter-spacing: 0.5px;
    color: var(--brand-text);
    white-space: nowrap;
  }
  .brand-dot {
    width: 22px;
    height: 22px;
    border-radius: 50%;
    background: var(--rose-gold);
  }
  .sender {
    position: absolute;
    left: 39px;
    top: 1018px;
    font-family: "Questrial", sans-serif;
    font-size: 17px;
    line-height: 24.5px;
    color: var(--ink);
    font-style: normal;
  }
  .sender .sender-name { font-size: 15px; }
</style>
</head>
<body>
<main class="canvas">
  <section class="letterhead">
    <svg class="header-band" viewBox="0 0 820 120" aria-hidden="true">
      <path d="M0 0 H820 V100 C 660 90, 470 82, 320 86 C 200 89, 90 98, 0 106 Z"/>
    </svg>
    <div class="brand">
      <span class="brand-dot"></span>
      <span class="brand-name">Brovanek Data</span>
    </div>
    <address class="sender">
      <div class="sender-name">Mara Delcourt, PhD</div>
      <div>418 NE Cedar Hollow Road, Ste 2107</div>
      <div>Lake Verna, TX 76512</div>
      <div>1-800-555-0147</div>
      <div>mara@brovanek-data.com</div>
    </address>
  </section>
</main>
</body>
</html>
```